Create a memorable Stationary for Security Software Company

Velbrantix is the worldwide leader in securing the Internet. Making Internet communications and critical data secure, reliable and available everywhere has been and continues to be our ongoing vision. We are committed to staying focused on real customer needs and to developing new and innovative security solutions that redefine the security landscape.

Industry/Entity Type

Internet

Font styles to use
Serif
Sans Serif
Script

Colors
0792cd
33a6d7
85cae6

```html
<!DOCTYPE html>
<html lang="en">
<head>
<meta charset="utf-8">
<title>Velbrantix Business Card</title>
<link href="https://fonts.googleapis.com/css2?family=Open+Sans:wght@400;600;700&display=swap" rel="stylesheet">
<style>
  :root {
    --blue-deep: #0792cd;
    --blue-mid: #33a6d7;
    --blue-light: #85cae6;
    --ink: #333333;
    --paper: #ffffff;
    --backdrop: #f1eee8;
    --edge: #3a3a3a;
  }
  * { margin: 0; padding: 0; box-sizing: border-box; }
  html, body {
    width: 1200px; height: 1118px; overflow: hidden;
    background: var(--backdrop);
    font-family: "Open Sans", Arial, sans-serif;
  }
  .canvas { position: relative; width: 1200px; height: 1118px; }

  .card {
    position: absolute;
    width: 819px; height: 468px;
    border-radius: 28px;
    border: 1px solid var(--edge);
    overflow: hidden;
  }
  .card-front { left: 58px; top: 50px; background: var(--paper); }
  .card-back { left: 329px; top: 586px; background: var(--blue-light); }

  .swoosh { position: absolute; inset: 0; width: 100%; height: 100%; }

  .brand-name {
    position: absolute;
    font-weight: 700;
    color: var(--blue-mid);
    white-space: nowrap;
    transform: translateX(-50%);
  }
  .card-front .brand-name { left: 233px; top: 150px; font-size: 52px; }
  .card-back .brand-name { left: 410px; top: 170px; font-size: 62px; color: var(--blue-deep); }

  .holder { position: absolute; right: 155px; top: 42px; text-align: right; }
  .holder-name { font-size: 33px; font-weight: 700; color: var(--blue-deep); line-height: 1.2; }
  .holder-title { font-size: 27px; font-weight: 400; color: var(--ink); line-height: 1.3; }

  .contact-list { position: absolute; right: 30px; top: 272px; list-style: none; text-align: right; }
  .contact-list li {
    display: flex; justify-content: flex-end; align-items: center; gap: 8px;
    font-size: 20px; color: var(--paper); height: 34px;
  }
  .contact-list svg { width: 17px; height: 17px; }

  .address { position: absolute; right: 30px; top: 426px; font-size: 20px; color: var(--paper); }

  .back-web {
    position: absolute; left: 0; right: 0; top: 356px;
    text-align: center; font-size: 27px; letter-spacing: 4px; color: var(--ink);
  }
</style>
</head>
<body>
<main class="canvas">
  <section class="card card-front">
    <svg class="swoosh" viewBox="0 0 661 378" preserveAspectRatio="none" aria-hidden="true">
      <path fill="var(--blue-deep)" d="M0,312 C160,358 360,322 482,205 C570,122 628,56 661,14 L661,378 L0,378 Z"/>
      <path fill="var(--blue-mid)" d="M0,276 C150,340 360,302 472,206 C350,312 150,330 0,302 Z"/>
      <path fill="var(--paper)" d="M0,306 C150,346 360,316 480,205 C362,326 150,352 0,320 Z"/>
    </svg>

    <div class="brand-name">Velbrantix</div>

    <div class="holder">
      <div class="holder-name">Your Name</div>
      <div class="holder-title">Title</div>
    </div>

    <ul class="contact-list">
      <li>
        <svg viewBox="0 0 16 16" aria-hidden="true"><circle cx="8" cy="8" r="7" fill="none" stroke="#fff" stroke-width="1.4"/><path d="M5.5,4.5 L7,6 L6.2,7 C6.8,8.3 7.7,9.2 9,9.8 L10,9 L11.5,10.5 L10.4,11.6 C7.5,11 5,8.5 4.4,5.6 Z" fill="#fff"/></svg>
        <span>012-345-6789</span>
      </li>
      <li>
        <svg viewBox="0 0 16 16" aria-hidden="true"><rect x="4.5" y="1" width="7" height="14" rx="1.2" fill="none" stroke="#fff" stroke-width="1.4"/><rect x="6" y="3" width="4" height="4" fill="#fff"/><circle cx="8" cy="11.5" r="1" fill="#fff"/></svg>
        <span>012-345-6789</span>
      </li>
      <li>
        <svg viewBox="0 0 16 16" aria-hidden="true"><rect x="1.5" y="4" width="13" height="9" fill="#fff"/><path d="M1.5,4 L8,9 L14.5,4" fill="none" stroke="var(--blue-deep)" stroke-width="1.3"/></svg>
        <span>info@velbrantix.com.com</span>
      </li>
      <li>
        <svg viewBox="0 0 16 16" aria-hidden="true"><g fill="none" stroke="#fff" stroke-width="1.2"><circle cx="8" cy="8" r="6.5"/><ellipse cx="8" cy="8" rx="3" ry="6.5"/><path d="M1.5,8 H14.5 M2.5,4.8 H13.5 M2.5,11.2 H13.5"/></g></svg>
        <span>www.velbrantix.com.com</span>
      </li>
    </ul>

    <div class="address">Street Name, City Name, Zipcode-012345</div>
  </section>

  <section class="card card-back">
    <div class="brand-name">Velbrantix</div>
    <div class="back-web">www.velbrantix.com.com</div>
  </section>
</main>
</body>
</html>
```